Maplecrest Disability - Social Security Disability Attorneys

Our company is expanding to attract clients nationwide for our social security disability practice. We have a logo, but I am looking for a creative and elegant letterhead that projects an image of being technologically advanced but still professional enough for the legal field. I am looking for the "wow factor" combined with this is still professional enough for a law practice.

Requesting letterhead and business card design
Updates

Had to update and change the logo. The previous logo had a typo. Please send updates with the new logo for consideration. The letterhead and business cards should be professional enough to be used for a law firm. Thanks.

Industry/Entity Type

Law Practice, Law Firm, Healthcare Industry, Government

Colors

Designer to choose colors to be used in the design.

Requirements
Nice to have
• **Please create a vertical design for the business card**

```html
<!DOCTYPE html>
<html lang="en">
<head>
<meta charset="utf-8">
<title>Maplecrest Disability – Letterhead</title>
<link rel="stylesheet" href="https://fonts.googleapis.com/css2?family=Montserrat:wght@400;500;700&display=swap">
<style>
  :root {
    --backdrop: #e9e9eb;
    --paper: #ffffff;
    --brand-blue: #4a73e8;
    --brand-orange: #fb7f26;
    --ink: #2f2f33;
    --ink-soft: #4a4a50;
  }
  * { box-sizing: border-box; margin: 0; padding: 0; }
  html, body {
    width: 1200px; height: 960px; overflow: hidden;
    background: var(--backdrop);
    font-family: "Montserrat", Arial, sans-serif;
    color: var(--ink);
  }
  .letterhead {
    position: absolute; left: 280px; top: 27px;
    width: 640px; height: 906px;
    background: var(--paper);
    box-shadow: 0 6px 24px rgba(0,0,0,.14);
    overflow: hidden;
  }
  .letterhead__decor { position: absolute; inset: 0; width: 640px; height: 906px; }

  .brand {
    position: absolute; left: 48px; top: 80px;
    display: flex; align-items: center; gap: 8px;
  }
  .brand__dot { width: 12px; height: 12px; border-radius: 50%; background: var(--brand-orange); }
  .brand__name {
    font-size: 19px; font-weight: 500; letter-spacing: 1.5px;
    text-transform: uppercase; color: var(--brand-blue);
  }

  .contact {
    position: absolute; left: 356px; top: 122px;
    font-size: 9.5px; line-height: 15px; color: var(--ink);
    list-style: none;
  }
  .contact__item { display: flex; align-items: center; gap: 6px; white-space: nowrap; }
  .contact__icon { width: 10px; height: 10px; flex: none; }

  .letter { position: absolute; left: 70px; top: 214px; width: 500px; }
  .letter__date { font-size: 12px; margin-bottom: 18px; }
  .letter__block { font-size: 12px; line-height: 15px; margin-bottom: 16px; }
  .letter__salutation { font-size: 15px; font-weight: 700; margin: 4px 0 14px; }
  .letter__para { font-size: 11px; line-height: 15px; color: var(--ink-soft); margin-bottom: 16px; }
  .letter__closing { font-size: 11.5px; margin-top: 26px; }
  .letter__signature {
    width: 190px; height: 46px; margin-top: 12px; border-radius: 4px;
    background: linear-gradient(90deg, #ececee, #f7f7f8);
  }
</style>
</head>
<body>
  <article class="letterhead">
    <svg class="letterhead__decor" viewBox="0 0 640 906" aria-hidden="true">
      <path d="M300,0 H640 V92 Q460,80 300,0 Z" fill="var(--brand-blue)"/>
      <path d="M288,0 Q458,84 640,92 V106 Q452,96 288,0 Z" fill="var(--brand-orange)"/>
      <path d="M0,884 Q360,864 640,702 V906 H0 Z" fill="var(--brand-blue)"/>
      <path d="M0,870 Q360,848 640,686 V702 Q360,864 0,884 Z" fill="var(--brand-orange)"/>
    </svg>

    <header class="brand">
      <span class="brand__dot"></span>
      <span class="brand__name">Maplecrest Disability</span>
    </header>

    <ul class="contact">
      <li class="contact__item">Suite 4, Level 12, Harbour</li>
      <li class="contact__item">Street Westfield NSW 2100</li>
      <li class="contact__item">
        <svg class="contact__icon" viewBox="0 0 10 10"><circle cx="5" cy="5" r="5" fill="var(--brand-orange)"/><path d="M3,2.5 L4.2,2.5 L4.6,4 L4,4.5 Q4.8,5.8 5.6,6 L6,5.4 L7.5,5.8 L7.5,7 Q4,7.5 3,2.5 Z" fill="#fff"/></svg>
        555-014-2290
      </li>
      <li class="contact__item">
        <svg class="contact__icon" viewBox="0 0 10 10"><circle cx="5" cy="5" r="5" fill="var(--brand-orange)"/><rect x="2.3" y="3.2" width="5.4" height="3.8" fill="#fff"/><path d="M2.3,3.2 L5,5.3 L7.7,3.2" fill="none" stroke="var(--brand-orange)" stroke-width=".7"/></svg>
        info@maplecrestdisability.com
      </li>
      <li class="contact__item">
        <svg class="contact__icon" viewBox="0 0 10 10"><circle cx="5" cy="5" r="5" fill="var(--brand-orange)"/><circle cx="5" cy="5" r="2.7" fill="none" stroke="#fff" stroke-width=".7"/><path d="M2.3,5 H7.7 M5,2.3 Q3.6,5 5,7.7 Q6.4,5 5,2.3" fill="none" stroke="#fff" stroke-width=".6"/></svg>
        www.maplecrestdisability.com
      </li>
    </ul>

    <section class="letter">
      <p class="letter__date">January-03-2020</p>
      <p class="letter__block">Mr. Daniel Reeve<br>President</p>
      <p class="letter__block">Northbay Holdings<br>48 Alder Lane, Suite# 10<br>Riverton, State, 120417</p>
      <p class="letter__salutation">Dear Mr. Reeve</p>
      <p class="letter__para">Lorem ipsum dolor sit amet, consectetur adipisicing elit, sed do eiusmod tempor incididunt ut labore et dolore magna aliqua. Ut enim ad minim veniam, quis nostrud exercitation ullamco laboris nisi ut aliquip ex ea commodo consequat. Duis aute irure dolor in reprehenderit in voluptate velit esse cillum dolore eu fugiat nulla pariatur.</p>
      <p class="letter__para">Lorem ipsum dolor sit amet, consectetur adipisicing elit, sed do eiusmod tempor incididunt ut labore et dolore magna aliqua. Ut enim ad minim veniam, quis nostrud exercitation ullamco laboris nisi ut aliquip ex ea commodo consequat. Duis aute irure dolor in reprehenderit in voluptate velit esse cillum dolore eu fugiat nulla pariatur.</p>
      <p class="letter__para">Lorem ipsum dolor sit amet, consectetur adipisicing elit, sed do eiusmod tempor incididunt ut labore et dolore magna aliqua. Ut enim ad minim veniam, quis nostrud exercitation ullamco laboris nisi ut aliquip ex ea commodo consequat.</p>
      <p class="letter__para">Excepteur sint occaecat cupidatat non proident, sunt in culpa qui officia deserunt mollit anim id est laborum. re et dolore magnam aliquam quaerat voluptatem.</p>
      <p class="letter__closing">Regards</p>
      <div class="letter__signature" role="img" aria-label="Handwritten signature of Arthur Bennett"></div>
    </section>
  </article>
</body>
</html>
```